House-share and Room Rental Website (With Focus on the Bedroom Landing Page)

Looking for website design for our House-share (executive accommodation) and room rental business.

Our company name is: Lodgivo could also be written as LodGivo or lodgivo. Either is fine .. just looking for a nice clean catchy logo to go with the design.

EXAMPLES
These are examples of other websites in this field that are doing well. this is a kind of baseline.
https://nestpartners-example.com.au/
https://www.bunkora-example.com/
https://www.dwelzy-example.com/
https://www.habiquo-example.net/
https://www.cohabiscout-example.com.au/

Our business model is to rent rooms to people looking for high-quality accommodation. We fill the gap between those looking to rent rooms and those with rooms to rent. However, our model is slightly different from those already on the market as we looking to fill a massive gap in the market delivering upmarket rooms for rent.(Executive Accommodation) also in the back end will be coupled with a self management process in the back end.

We offer executive style accommodation that stands out above the rest. With special extras like fire safety.. and management processes that create happier homes. We are looking for a web design package that can help us grow and scale our business. We need a design that is captivating

Our MAIN focus is having a room landing page that stands out from the rest... The core of our business will rely on the promotion of the rooms in a share house... so the whole design relies on the BEDROOM landing page to drive results.

Target Market(s)

We have 2 markets we are aiming at ... the first market is people offering rooms to rent who want the highest rental return. The second market is people looking to rent safe, high-quality rooms, in houses that are well managed and looked after.

Industry/Entity Type

Share Economy

Logo Text

LodGivo

Number of Pages Required

5+ page

Font styles to use
Sans Serif

Colors
3276b5

Requirements
Must have
• A messaging system whereby we can create direct communication between those offering rooms and those looking for rooms.
• A call to action that says " Schedule an Inspection"
• Landing page for promoting rooms
• A home page for showing stock.
• Profile page for those selling rooms
• Profile page for those looking for rooms.
• A scheduling calendar for booking inspections
Nice to have
• Pages where new residents can lock in a room.. pay bond and rents.. and sign contracts
• Notifications
• SMS capabilities in the backend.
Should not have
• No script or handwriting fonts.

```html
<!DOCTYPE html>
<html lang="en">
<head>
<meta charset="utf-8">
<title>Lodgivo – Executive Accommodation for Two</title>
<link rel="stylesheet" href="https://fonts.googleapis.com/css2?family=Questrial&family=Open+Sans:wght@600&display=swap">
<style>
  :root{
    --brand:#3276b5;
    --brand-deep:#1b4f9a;
    --brand-mid:#3a74b8;
    --navy:#1d2f57;
    --ink:#1d2a6b;
    --link:#2b63b5;
    --muted:#555b66;
    --rule:#c9c9c9;
    --white:#ffffff;
  }
  *{box-sizing:border-box;margin:0;padding:0}
  html,body{width:714px;height:1200px;overflow:hidden;background:var(--white)}
  body{position:relative;font-family:"Questrial",sans-serif;color:var(--ink)}

  .site-header{position:absolute;left:0;top:0;width:714px;height:72px;display:flex;align-items:center;padding-left:20px;gap:8px}
  .brand-dot{width:22px;height:22px;border-radius:50%;background:var(--brand)}
  .brand-name{font-size:27px;color:var(--brand);letter-spacing:.5px}
  .header-rule{position:absolute;top:72px;left:0;width:714px;height:4px;background:var(--brand)}

  .hero{position:absolute;top:76px;left:0;width:714px;height:404px;text-align:center;color:var(--white)}
  .hero-photo{position:absolute;inset:0;background:linear-gradient(135deg,#3c3c3c 0%,#2a2a2a 45%,#4a4a4a 70%,#1e1e1e 100%)}
  .hero-content{position:relative}
  .hero-title{padding-top:102px;font-size:25px;font-weight:400;letter-spacing:.3px}
  .hero-text{margin-top:18px;font-family:"Open Sans",sans-serif;font-weight:600;font-size:10px;line-height:22px}
  .cta{display:inline-block;margin-top:17px;width:206px;height:37px;line-height:37px;border-radius:5px;background:var(--brand);color:var(--white);font-size:15.5px;text-decoration:none}
  .hero-arrow{position:absolute;top:146px}
  .hero-arrow.prev{left:18px}
  .hero-arrow.next{right:18px}

  .room-facts{position:absolute;top:480px;left:0;width:714px;height:47px;display:flex;list-style:none;color:var(--white)}
  .fact{display:flex;align-items:center;gap:9px;padding-left:12px;background:var(--brand-deep)}
  .fact.alt{background:var(--brand-mid)}
  .fact-label{font-size:10.5px;display:block}
  .fact-value{font-size:12.5px;display:block;margin-top:3px}

  .info-panel{position:absolute;top:559px;width:243px;height:206px;border:2px solid var(--rule);padding:16px 0 0 0}
  .info-panel.room{left:94px}
  .info-panel.public{left:381px}
  .panel-title{font-size:12px;font-weight:400;color:var(--ink)}
  .room .panel-title{padding-left:52px}
  .public .panel-title{padding-left:32px}
  .amenity-list{list-style:none;margin-top:4px}
  .amenity-list li{font-size:12.2px;color:var(--link);height:22.4px;line-height:22.4px;display:flex}
  .amenity-list li::before{content:"❖";color:#777;font-size:9px;width:27px}
  .room .amenity-list li{padding-left:30px}
  .public .amenity-list li{padding-left:38px}
  .core-title{padding-left:27px;margin-top:5px}
  .core-facts{margin-top:10px;padding-left:27px;font-size:10.5px}
  .core-facts div{display:flex;height:22.4px;align-items:center}
  .core-facts dt{color:var(--link);width:51px}
  .core-facts dd{color:var(--muted)}

  .location-map{position:absolute;left:271px;top:816px;width:186px;height:166px;border:2px solid #a9c4e4;background:linear-gradient(135deg,#e6e3dc,#d8d6cf 60%,#e9e6de)}

  .site-footer{position:absolute;top:983px;left:0;width:714px;height:217px;color:var(--white)}
  .footer-bg{position:absolute;inset:0}
  .footer-col{position:absolute;top:71px;font-size:12px;line-height:17.6px}
  .footer-col h2{font-size:15px;font-weight:400;margin-bottom:7px}
  .footer-col.contact{left:12px}
  .footer-col.contact p{padding-left:2px}
  .footer-col.links{left:593px}
  .footer-col.links a{display:block;color:var(--white);text-decoration:none}
  .footer-brand{position:absolute;left:198px;top:92px;display:flex;align-items:center;gap:12px}
  .footer-brand .brand-dot{width:36px;height:36px;background:var(--white)}
  .footer-brand .brand-name{font-size:48px;color:var(--white)}
  .footer-bar{position:absolute;left:0;bottom:0;width:714px;height:20px;background:var(--navy);display:flex;justify-content:space-between;align-items:center;padding:0 10px 0 12px;font-size:9.5px;font-family:"Open Sans",sans-serif}
  .footer-bar a{color:var(--white);text-decoration:none}
</style>
</head>
<body>

<header class="site-header">
  <span class="brand-dot"></span>
  <span class="brand-name">lodgivo</span>
</header>
<div class="header-rule"></div>

<section class="hero">
  <div class="hero-photo" role="img" aria-label="Photo of a dim modern bedroom with a bed against a concrete wall"></div>
  <div class="hero-content">
    <h1 class="hero-title">EXCEUTIVE ACCOMODATION FOR TWO</h1>
    <p class="hero-text">Looking for website design for our Houseshare and room rental business.<br>Our business model is to rent rooms to people looking for high quality<br>accommodation.</p>
    <a class="cta" href="#">Schedule an Inspection</a>
  </div>
  <svg class="hero-arrow prev" width="38" height="52" viewBox="0 0 38 52"><polyline points="36,2 3,26 36,50" fill="none" stroke="#ffffff" stroke-width="2"/></svg>
  <svg class="hero-arrow next" width="38" height="52" viewBox="0 0 38 52"><polyline points="2,2 35,26 2,50" fill="none" stroke="#3a86d4" stroke-width="2"/></svg>
</section>

<ul class="room-facts">
  <li class="fact" style="width:137px">
    <svg width="30" height="26" viewBox="0 0 30 26" fill="none" stroke="#fff" stroke-width="2"><rect x="4" y="3" width="18" height="14"/><path d="M1 22h28"/><circle cx="20" cy="8" r="6" fill="#1b4f9a"/><path d="M20 8l3-3"/></svg>
    <div><span class="fact-label">INTERNET SPEED</span><span class="fact-value">2 mbps</span></div>
  </li>
  <li class="fact alt" style="width:121px;padding-left:16px">
    <svg width="44" height="22" viewBox="0 0 44 22" fill="#fff"><rect x="1" y="2" width="3" height="19"/><rect x="40" y="8" width="3" height="13"/><rect x="4" y="12" width="36" height="5"/><circle cx="9" cy="9" r="3"/><rect x="14" y="8" width="26" height="4" rx="2"/></svg>
    <div><span class="fact-label">BED SIZE</span><span class="fact-value">6 by 6</span></div>
  </li>
  <li class="fact" style="width:150px">
    <svg width="26" height="28" viewBox="0 0 26 28" fill="none" stroke="#fff" stroke-width="2.2"><circle cx="10" cy="13" r="6"/><path d="M10 19v8M6 24h8M14 9l8-7M17 2h5v5"/></svg>
    <div><span class="fact-label">GENDER PREFERENCE</span><span class="fact-value">Couple</span></div>
  </li>
  <li class="fact alt" style="width:117px">
    <svg width="26" height="32" viewBox="0 0 26 32" fill="none" stroke="#fff" stroke-width="2.2"><path d="M13 24C6 15 5 12 5 10a8 8 0 0 1 16 0c0 2-1 5-8 14z"/><circle cx="13" cy="10" r="3"/><ellipse cx="13" cy="27" rx="10" ry="3"/></svg>
    <div><span class="fact-label">ROOM AREA</span><span class="fact-value">400 sqm</span></div>
  </li>
  <li class="fact" style="width:189px">
    <svg width="30" height="30" viewBox="0 0 30 30" fill="none" stroke="#fff" stroke-width="2"><path d="M5 14V5a3 3 0 0 1 6 0"/><path d="M14 6l-3 3M16 9l-3 3"/><rect x="2" y="14" width="26" height="4" fill="#fff"/><path d="M4 18l2 8h18l2-8M8 26v3M22 26v3"/></svg>
    <div><span class="fact-label">BATHROOM TYPE</span><span class="fact-value">Shared</span></div>
  </li>
</ul>

<section class="info-panel room">
  <h2 class="panel-title">ROOM AMENITIES</h2>
  <ul class="amenity-list">
    <li>Furnished/unfurnished</li>
    <li>TV</li>
    <li>Storage space</li>
    <li>Study Desk / Workstation</li>
    <li>Wardrobe</li>
    <li>Ensuite shower</li>
    <li>Kitchenette</li>
  </ul>
</section>

<section class="info-panel public">
  <h2 class="panel-title">PUBLIC AMMENITIES</h2>
  <ul class="amenity-list">
    <li>Transport options</li>
    <li>Trains</li>
    <li>Busses</li>
    <li>50 miles from Washington DC</li>
  </ul>
  <h2 class="panel-title core-title">CORE INFOMATION</h2>
  <dl class="core-facts">
    <div><dt>ADRESS</dt><dd>Abc Street, NY Town</dd></div>
    <div><dt>UTILITIES</dt><dd>Included</dd></div>
  </dl>
</section>

<div class="location-map" role="img" aria-label="Street map showing the route to the property"></div>

<footer class="site-footer">
  <svg class="footer-bg" width="714" height="217" viewBox="0 0 714 217" preserveAspectRatio="none">
    <polygon points="0,0 357,40 714,0 714,217 0,217" fill="#3276b5"/>
    <polygon points="0,0 357,40 714,0 714,12 357,52 0,12" fill="#1b4f9a"/>
  </svg>
  <div class="footer-col contact">
    <h2>CONTACT US</h2>
    <p>Elmfield Street 1234</p>
    <p>NY, Example</p>
    <p>info@roomhaven-example.com</p>
    <p>www.roomhaven-example.com</p>
  </div>
  <div class="footer-brand">
    <span class="brand-dot"></span>
    <span class="brand-name">lodgivo</span>
  </div>
  <nav class="footer-col links">
    <h2>QUICK LINKS</h2>
    <a href="#">Bedrooms</a>
    <a href="#">Sitting Rooms</a>
    <a href="#">Homes</a>
  </nav>
  <div class="footer-bar">
    <span>© Roomhaven Ltd 2019</span>
    <span><a href="#">Terms</a> | <a href="#">Privacy Policy</a></span>
  </div>
</footer>

</body>
</html>
```